Brightwell Supports

We need an updated website that captures the comprehensive services and supports we provide to persons with developmental disabilities. We need a website design that educates families about the services we provide. We would also need a website that is user-friendly so that we could periodically update training schedules and ongoing programming.

• Thank you for submitting designs.  A few things I am hoping to see offered in the website:
• Front page highlights the services we offer (host homes, family caregiver, day program, employment program, SLS program, supported apartment program, behavior/clinical program)
• Front page also highlights any new programs we want to make prominent:  family caregiver, future restaurant employment openings, etc...
• Interactive Training Calendar
• Employee Resources page (link to carevo, email login, etc.)
• Uniform provider application for host home providers
• Information on agency - history, goals, etc.
• Contact Information/Location

 

Fun things to include:

• Client Highlights (featuring a client story each month, etc...)
• Employee highlights (featuring a staff member...)
• link to other Brightwell business pages (Brightwell Therapy and Brightwell Restaurant)

```html
<!DOCTYPE html>
<html lang="en">
<head>
<meta charset="utf-8">
<title>Brightwell Supports – Training Calendar</title>
<link href="https://fonts.googleapis.com/css2?family=Lato:ital,wght@0,300;0,400;0,700;0,900;1,300&display=swap" rel="stylesheet">
<style>
:root{
  --topbar:#8a8a8c;
  --maroon:#6e1422;
  --rust:#8b3b37;
  --mission:#727275;
  --dark:#3c3c3e;
  --quote:#737376;
  --footer:#8b8b8d;
  --ink:#2a2a2a;
  --white:#ffffff;
  --grid:#d9d9d9;
  --row-a:#8f8f92;
  --row-b:#78787b;
}
*{box-sizing:border-box;margin:0;padding:0}
html,body{width:794px;height:1200px;overflow:hidden}
body{position:relative;font-family:'Lato',sans-serif;background:var(--white);color:var(--ink)}
.abs{position:absolute}

/* top bar */
.topbar{left:0;top:0;width:794px;height:24px;background:var(--topbar);color:var(--white);font-size:7px;letter-spacing:.5px}
.topbar .social{left:133px;top:7px;display:flex;gap:7px}
.topbar .social span{width:10px;height:10px;border-radius:50%;background:var(--white);display:block}
.topbar .contact{left:388px;top:0;height:24px;display:flex;align-items:center;gap:12px}
.topbar .contact span{display:flex;align-items:center;gap:4px}

/* header */
.header{left:0;top:24px;width:794px;height:54px;background:var(--white)}
.logo{left:117px;top:16px;display:flex;align-items:center;gap:6px}
.logo i{width:16px;height:16px;background:var(--maroon);border-radius:50%;display:block}
.logo span{font-size:15px;font-weight:900;color:var(--maroon);letter-spacing:.3px}
.nav{left:316px;top:0;height:54px;display:flex;font-size:6.5px;font-weight:700;color:var(--maroon);letter-spacing:.5px}
.nav a{display:flex;align-items:center;justify-content:center;text-align:center;padding:0 9px;color:inherit;text-decoration:none;line-height:1.2;position:relative}
.nav a+a::before{content:"";position:absolute;left:0;top:20px;height:14px;border-left:1px solid #cfcfcf}
.nav a.active{background:var(--maroon);color:var(--white);width:50px;padding:0}
.nav a.active::before,.nav a.active+a::before{display:none}

.crumb{left:0;top:78px;width:794px;height:18px;background:var(--maroon);color:var(--white);font-size:6px;padding:6px 0 0 122px}

/* calendar region */
.stage{left:0;top:96px;width:794px;height:387px;background:var(--rust)}
.calendar{left:112px;top:122px;width:371px;height:334px;background:var(--white)}
.calendar h1{height:63px;display:flex;align-items:center;justify-content:center;font-size:25px;font-weight:900;letter-spacing:5px;color:var(--maroon)}
.calendar .band{height:24px;background:#a3a3a6;color:var(--white);font-weight:300;font-size:14px;padding:3px 0 0 26px}
.days{display:grid;grid-template-columns:repeat(7,1fr);height:10px;background:var(--maroon);color:var(--white);font-size:6px;font-weight:700;text-align:center;line-height:10px}
.cells{display:grid;grid-template-columns:repeat(7,1fr);grid-template-rows:repeat(5,47px)}
.cell{border-right:1px solid var(--grid);border-bottom:1px solid var(--grid);position:relative;text-align:center;font-size:4.5px;color:#444;padding-top:11px}
.cell:nth-child(7n){border-right:none}
.cell .num{position:absolute;right:4px;top:2px;font-size:6px;color:#aaa}
.cell b{display:block;color:var(--maroon);font-size:5px;font-weight:700}
.cell.today{background:var(--maroon);color:var(--white)}
.cell.today b,.cell.today .num{color:var(--white)}

.programs{left:500px;top:122px;width:175px;background:var(--row-b)}
.programs h2{height:31px;background:var(--white);color:var(--maroon);font-size:11px;font-weight:900;letter-spacing:.5px;padding:11px 0 0 20px}
.programs li{list-style:none;height:17.2px;font-size:5.5px;color:var(--white);padding:6px 0 0 7px;background:var(--row-a)}
.programs li:nth-child(even){background:var(--row-b)}

/* mission */
.mission{left:0;top:483px;width:794px;height:113px;background:var(--mission);color:var(--white);text-align:center}
.mission h2{margin-top:15px;font-size:17px;font-weight:900;letter-spacing:1px}
.rule{width:90px;height:1px;background:var(--white);margin:4px auto 0}
.mission p{margin-top:16px;font-size:11px;font-weight:300;line-height:1.75}

/* client highlights */
.clients{left:0;top:596px;width:794px;height:377px;background:var(--dark);color:var(--white)}
.clients h2{position:absolute;left:213px;top:18px;font-size:16px;font-weight:900;letter-spacing:.5px}
.clients h2::after{content:"";display:block;width:150px;height:1px;background:var(--white);margin-top:4px}
.month-tab{left:449px;top:0;width:115px;height:47px;background:var(--white);color:#3c3c3e;font-size:16px;font-weight:900;text-align:center;padding-top:15px;letter-spacing:.5px}
.month-tab::after{content:"";position:absolute;left:50px;bottom:-7px;border:7px solid transparent;border-top-color:var(--white);border-bottom:0}
.person{position:absolute;top:78px;width:175px;text-align:center}
.portrait{width:106px;height:106px;border-radius:50%;margin:0 auto;border:2px solid var(--maroon);background:linear-gradient(180deg,#d9d4cf 0%,#b89a86 100%)}
.person h3{margin-top:20px;font-size:10px;font-weight:900;letter-spacing:.3px;white-space:nowrap}
.person p{margin:18px auto 0;width:150px;text-align:left;font-size:6.4px;font-weight:400;line-height:1.85}
.person .links{margin-top:25px;display:flex;justify-content:center;gap:11px}
.person .links span{width:15px;height:15px;border-radius:50%;background:var(--white);display:block}

/* testimonial */
.quote{left:0;top:973px;width:794px;height:89px;background:var(--quote);color:var(--white)}
.quote svg{position:absolute;left:145px;top:19px}
.quote blockquote{position:absolute;right:194px;top:24px;text-align:right;font-size:10.5px;font-style:italic;font-weight:300;line-height:1.45}
.quote cite{display:block;font-style:normal;font-weight:700;font-size:7.5px;margin-top:4px}

/* footer */
.footer{left:0;top:1062px;width:794px;height:127px;background:var(--footer);color:var(--white);font-size:5.5px}
.fcol{position:absolute;top:32px}
.fcol h4{font-size:6px;font-weight:700;letter-spacing:.6px;padding-bottom:4px;border-bottom:1px solid #b5b5b7;margin-bottom:8px;white-space:nowrap}
.fcol p{line-height:1.9}
.subscribe input{display:block;width:105px;height:8px;border:none;background:var(--white);font-size:4.5px;padding-left:3px;margin-top:4px;font-family:inherit}
.subscribe button{display:block;width:72px;height:7px;border:none;background:var(--maroon);color:var(--white);font-size:4px;margin-top:3px;font-family:inherit}
.legal{left:0;top:1189px;width:794px;height:11px;background:#2b2b2b;color:var(--white);font-size:5.5px;letter-spacing:1.2px;text-align:center;line-height:11px}
</style>
</head>
<body>

<div class="abs topbar">
  <div class="abs social" aria-label="Social links"><span></span><span></span><span></span><span></span><span></span></div>
  <div class="abs contact">
    <span>24/7 SUPPORT
      <svg width="8" height="8" viewBox="0 0 10 10"><path d="M2 0h2l1 3-1.5 1a6 6 0 0 0 2.5 2.5L7 5l3 1v2c0 1-1 2-2 2A8 8 0 0 1 0 2c0-1 1-2 2-2z" fill="#fff"/></svg>
      +1 555 010 2468</span>
    <span><svg width="11" height="8" viewBox="0 0 11 8"><rect x=".5" y=".5" width="10" height="7" fill="none" stroke="#fff"/><path d="M.5.5l5 4 5-4" fill="none" stroke="#fff"/></svg>INFO@BRIGHTWELLSUPPORTS.ORG</span>
    <span><svg width="8" height="8" viewBox="0 0 10 10"><circle cx="4" cy="4" r="3" fill="none" stroke="#fff" stroke-width="1.5"/><path d="M6.5 6.5L9.5 9.5" stroke="#fff" stroke-width="1.5"/></svg>SEARCH</span>
  </div>
</div>

<header class="abs header">
  <div class="abs logo"><i></i><span>Brightwell Supports</span></div>
  <nav class="abs nav">
    <a>SERVICES</a>
    <a>BECOME A<br>PROVIDER</a>
    <a class="active">PROGRAMS</a>
    <a>LOCATION</a>
    <a>COMMUNITY<br>RESOURCES</a>
    <a>SUPPORT</a>
    <a>OUR TEAM</a>
  </nav>
</header>
<div class="abs crumb">Home &nbsp;›&nbsp; Calendar</div>

<div class="abs stage"></div>

<section class="abs calendar">
  <h1>APRIL</h1>
  <div class="band">Training Calendar</div>
  <div class="days"><span>MON</span><span>MON</span><span>MON</span><span>MON</span><span>MON</span><span>MON</span><span>MON</span></div>
  <div class="cells">
    <div class="cell"><span class="num">1</span></div>
    <div class="cell"><span class="num">2</span></div>
    <div class="cell"><span class="num">3</span><b>Training Calendar</b>7:30pm - 8:30 pm<br><strong>$10</strong></div>
    <div class="cell"><span class="num">4</span></div>
    <div class="cell"><span class="num">5</span></div>
    <div class="cell"><span class="num">6</span></div>
    <div class="cell"><span class="num">7</span></div>

    <div class="cell"><span class="num">8</span></div>
    <div class="cell"><span class="num">9</span></div>
    <div class="cell"><span class="num">10</span></div>
    <div class="cell"><span class="num">11</span><b>Training Calendar</b>7:30pm - 8:30 pm<br><strong>$10</strong></div>
    <div class="cell"><span class="num">12</span><b>Training Calendar</b>7:30pm - 8:30 pm<br><strong>$10</strong></div>
    <div class="cell"><span class="num">13</span></div>
    <div class="cell"><span class="num">14</span></div>

    <div class="cell"><span class="num">15</span></div>
    <div class="cell"><span class="num">16</span><b>Training Calendar</b>7:30pm - 8:30 pm<br><strong>$10</strong></div>
    <div class="cell"><span class="num">17</span></div>
    <div class="cell"><span class="num">18</span><b>Training Calendar</b>7:30pm - 8:30 pm<br><strong>$10</strong></div>
    <div class="cell"><span class="num">19</span></div>
    <div class="cell"><span class="num">20</span><b>Training Calendar</b>7:30pm - 8:30 pm<br><strong>$10</strong></div>
    <div class="cell"><span class="num">21</span></div>

    <div class="cell"><span class="num">22</span></div>
    <div class="cell"><span class="num">23</span><b>Training Calendar</b>7:30pm - 8:30 pm<br><strong>$10</strong></div>
    <div class="cell"><span class="num">24</span></div>
    <div class="cell today"><span class="num">25</span><b>Training Calendar</b>7:30pm - 8:30 pm<br><strong>$10</strong></div>
    <div class="cell"><span class="num">26</span></div>
    <div class="cell"><span class="num">27</span><b>Training Calendar</b>7:30pm - 8:30 pm<br><strong>$10</strong></div>
    <div class="cell"><span class="num">28</span></div>

    <div class="cell"><span class="num">29</span></div>
    <div class="cell"><span class="num">30</span></div>
    <div class="cell"><span class="num">1</span><b>Training Calendar</b>7:30pm - 8:30 pm<br><strong>$10</strong></div>
    <div class="cell"><span class="num">2</span><b>Training Calendar</b>7:30pm - 8:30 pm<br><strong>$10</strong></div>
    <div class="cell"><span class="num">3</span><b>Training Calendar</b>7:30pm - 8:30 pm<br><strong>$10</strong></div>
    <div class="cell"><span class="num">4</span><b>Training Calendar</b>7:30pm - 8:30 pm<br><strong>$10</strong></div>
    <div class="cell"><span class="num">5</span></div>
  </div>
</section>

<aside class="abs programs">
  <h2>PROGRAMS</h2>
  <ul>
    <li>Family Caregiver</li>
    <li>Future Restaurant Employment openings</li>
    <li>Future Restaurant</li>
    <li>Future Restaurant Employment openings</li>
    <li>Future Restaurant</li>
    <li>Future Restaurant Employment openings</li>
    <li>Future Restaurant</li>
    <li>Future Restaurant Employment openings</li>
  </ul>
</aside>

<section class="abs mission">
  <h2>MISSION &nbsp;STATEMENT</h2>
  <div class="rule"></div>
  <p>To promote relationships, attachment, positive boundaries, and resource development<br>to create opportunities and improve the lives of people living with disabilities.</p>
</section>

<section class="abs clients">
  <h2>CLIENT HIGHLIGHTS</h2>
  <div class="abs month-tab">APRIL</div>

  <article class="person" style="left:104px">
    <div class="portrait" role="img" aria-label="Portrait photo of featured client"></div>
    <h3>DANA BRIGHTWELL, CLIENT</h3>
    <p>Dana has a passion for art and music and has made both a meaningful part of her life. Dana joined our day program three years ago and now helps lead a weekly painting group, sharing her work with friends and family at the center.</p>
    <div class="links" aria-label="Profile links"><span></span><span></span><span></span></div>
  </article>

  <article class="person" style="left:288px">
    <div class="portrait" role="img" aria-label="Portrait photo of featured client"></div>
    <h3>DANA BRIGHTWELL, CLIENT</h3>
    <p>Dana has a passion for art and music and has made both a meaningful part of her life. Dana joined our day program three years ago and now helps lead a weekly painting group, sharing her work with friends and family at the center.</p>
    <div class="links" aria-label="Profile links"><span></span><span></span><span></span></div>
  </article>

  <article class="person" style="left:473px">
    <div class="portrait" role="img" aria-label="Portrait photo of featured client"></div>
    <h3>DANA BRIGHTWELL, CLIENT</h3>
    <p>Dana has a passion for art and music and has made both a meaningful part of her life. Dana joined our day program three years ago and now helps lead a weekly painting group, sharing her work with friends and family at the center.</p>
    <div class="links" aria-label="Profile links"><span></span><span></span><span></span></div>
  </article>
</section>

<section class="abs quote">
  <svg width="56" height="50" viewBox="0 0 56 50" aria-hidden="true">
    <path d="M0 0h56v38H22L8 50V38H0z" fill="#8e8e91"/>
    <rect x="10" y="10" width="36" height="3" fill="#737376"/>
    <rect x="10" y="17" width="36" height="3" fill="#737376"/>
    <rect x="10" y="24" width="24" height="3" fill="#737376"/>
  </svg>
  <blockquote>“Praesent vestibulum aenean nonummy hendrerit mauris! Whether you<br>need a motor for a precise medical application.”
    <cite>Mark Ellison, CEO Fenwick Motors</cite>
  </blockquote>
</section>

<footer class="abs footer">
  <div class="fcol" style="left:129px;width:96px">
    <h4>ABOUT US</h4>
    <p>123 Alder Lane<br>Springvale, CO 80000<br>Phone: 555-010-4101<br>Fax: 555-010-8216</p>
  </div>
  <div class="fcol" style="left:275px;width:90px">
    <h4>COMPANY</h4>
    <p>About<br>Career<br>Media Kit<br>Contact Us</p>
  </div>
  <div class="fcol subscribe" style="left:407px;width:108px">
    <h4>SUBSCRIBE TO OUR NEWSLETTER</h4>
    <p>Get monthly updates, training<br>dates and news.</p>
    <input type="text" placeholder="Email Address" aria-label="Email address">
    <button type="button">Subscribe</button>
  </div>
  <div class="fcol" style="left:575px;width:90px">
    <h4>HELP &amp; SUPPORT</h4>
    <p>Terms<br>Privacy<br>Sign Up<br>Log In</p>
  </div>
</footer>
<div class="abs legal">© 2014 &nbsp;ALL RIGHTS RESERVED &nbsp;PRIVACY POLICY</div>

</body>
</html>
```